The design should look similar to the uploaded example to accommodate the information needed for a business card template. I would like to see the colors orange and charcoal grey incorporated along with the logo.The following should be on the back of the card SPECIALIZING IN NEW AND USED TIRES & WHEELS FOR:- Loaders- Skid Steers- Telehandlers- Boom Lifts- Forklifs and moreELIMINATING DOWNTIMEWheel Exchange Program for New & Used Foam Filled and Solid Rubber TiresSPECIALTY SERVICES- Foam Filling Tires- Largest Tire Press in SE- ONSITE Forklift Tire Press- Boom Truck Services - Rubber Tracks

Target Market(s)

New and Existing Customers

Industry/Entity Type

Business

Contact Information for Business Card

NAMEHEAVY DUTY TIRE, LLC8470 Belvedere RoadWest Palm Beach, FL 33411P: 844-HD-TIRESF: 561-431-6469C:E: W: WWW.GRANITERIMSUPPLY-EXAMPLE.COM

Font styles to use
Sans Serif

Colors
f37122
333333

Requirements
Must have
• The logo and the information indicated for the backside of the card
Nice to have
• Keep the orange and charcoal grey colors

```html
<!DOCTYPE html>
<html lang="en">
<head>
<meta charset="utf-8">
<title>Granite Rim Supply – Business Card</title>
<link href="https://fonts.googleapis.com/css2?family=Roboto+Slab:wght@800&family=Open+Sans:wght@400;600;700&display=swap" rel="stylesheet">
<style>
  :root{
    --orange:#f37122;
    --charcoal:#3c434a;
    --charcoal-deep:#333333;
    --white:#ffffff;
    --stage:#e7e4df;
  }
  *{box-sizing:border-box;margin:0;padding:0}
  html,body{width:1200px;height:843px;overflow:hidden}
  body{background:var(--stage);font-family:"Open Sans",sans-serif;position:relative}
  .card{position:absolute;left:280px;width:640px;height:366px;overflow:hidden;box-shadow:0 6px 18px rgba(0,0,0,.25)}
  .card--back{top:36px;background:var(--charcoal)}
  .card--front{top:442px;background:var(--white)}

  /* back */
  .back-mark{position:absolute;left:34px;top:40px;width:270px;height:270px;border-radius:50%;background:var(--orange);display:flex;align-items:center;justify-content:center;text-align:center}
  .back-mark__name{font-family:"Roboto Slab",serif;font-weight:800;font-size:40px;line-height:1.05;color:var(--charcoal-deep)}
  .services{position:absolute;right:30px;top:40px;text-align:right;width:330px}
  .services__heading{font-weight:700;font-size:15px;line-height:1.2;color:var(--orange);text-transform:uppercase;margin-top:12px}
  .services__heading:first-child{margin-top:0}
  .services__line{font-size:13.5px;line-height:1.35;color:var(--white)}
  .dot{display:inline-block;width:7px;height:7px;border-radius:50%;background:var(--orange);margin:0 5px;vertical-align:middle}

  /* front */
  .front-panel{position:absolute;inset:0}
  .brand{position:absolute;left:34px;top:90px;display:flex;align-items:center;gap:14px}
  .brand__circle{width:58px;height:58px;border-radius:50%;background:var(--orange);flex:none}
  .brand__name{font-family:"Roboto Slab",serif;font-weight:800;font-size:21px;line-height:1.15;color:var(--charcoal-deep);text-transform:uppercase}
  .contact{position:absolute;right:28px;top:72px;text-align:right;color:var(--white)}
  .contact__name{font-family:"Roboto Slab",serif;font-weight:800;font-size:22px;letter-spacing:.5px}
  .contact__title{font-size:14px;font-weight:600;margin-bottom:14px}
  .contact__address{font-size:14px;line-height:1.35;margin-bottom:10px}
  .contact__row{font-size:14px;line-height:1.55;display:flex;justify-content:flex-end;align-items:center;gap:8px}
  .contact__row svg{width:15px;height:15px;flex:none}
</style>
</head>
<body>

<section class="card card--back">
  <div class="back-mark"><span class="back-mark__name">GRANITE<br>RIM</span></div>
  <div class="services">
    <p class="services__heading">Specializing in new and<br>used tires &amp; wheels for</p>
    <p class="services__line">Loaders<span class="dot"></span>Skid Steers<span class="dot"></span>Telehandlers<span class="dot"></span></p>
    <p class="services__line">Boom Lifts<span class="dot"></span>Forklifts and more<span class="dot"></span></p>
    <p class="services__heading">Eliminating downtime</p>
    <p class="services__line">Wheel Exchange Program for New &amp;<span class="dot"></span></p>
    <p class="services__line">Used Foam Filled and Solid Rubber Tires</p>
    <p class="services__heading">Specialty services</p>
    <p class="services__line">Foam Filling Tires<span class="dot"></span></p>
    <p class="services__line">Largest Tire Press in SE<span class="dot"></span></p>
    <p class="services__line">ONSITE Forklift Tire Press<span class="dot"></span></p>
    <p class="services__line">Boom Truck Services<span class="dot"></span>Rubber Tracks<span class="dot"></span></p>
  </div>
</section>

<section class="card card--front">
  <svg class="front-panel" viewBox="0 0 640 366" preserveAspectRatio="none" aria-hidden="true">
    <path d="M228 366 C298 300 288 140 328 70 C348 35 375 10 404 0 L640 0 L640 366 Z" fill="#f37122"/>
    <path d="M250 366 C316 300 306 150 346 80 C366 42 390 20 418 0 L640 0 L640 366 Z" fill="#3c434a"/>
  </svg>
  <div class="brand">
    <span class="brand__circle"></span>
    <span class="brand__name">Granite Rim<br>Supply LLC</span>
  </div>
  <div class="contact">
    <p class="contact__name">DANA WHITFIELD</p>
    <p class="contact__title">CEO/FOUNDER</p>
    <p class="contact__address">5126 Marston Lane<br>West Palm Beach, FL 33411</p>
    <p class="contact__row">844-GR-WHEEL
      <svg viewBox="0 0 16 16"><path fill="#fff" d="M3 1l3 3-2 2c1 2 3 4 5 5l2-2 3 3-2 3C6 15 1 10 1 3z"/></svg></p>
    <p class="contact__row">836 512 7740
      <svg viewBox="0 0 16 16"><rect x="4" y="1" width="8" height="14" rx="1.5" fill="none" stroke="#fff" stroke-width="1.6"/><circle cx="8" cy="12.5" r="1" fill="#fff"/></svg></p>
    <p class="contact__row">561-278-9053
      <svg viewBox="0 0 16 16"><rect x="1" y="6" width="14" height="8" rx="1" fill="#fff"/><rect x="4" y="1" width="8" height="5" fill="none" stroke="#fff" stroke-width="1.4"/></svg></p>
    <p class="contact__row">name@example-mail.com
      <svg viewBox="0 0 16 16"><rect x="1" y="3" width="14" height="10" rx="1" fill="#fff"/><path d="M1.5 3.5 8 9l6.5-5.5" fill="none" stroke="#3c434a" stroke-width="1.3"/></svg></p>
    <p class="contact__row">www.graniterimsupply-example.com
      <svg viewBox="0 0 16 16"><circle cx="8" cy="8" r="6.5" fill="none" stroke="#fff" stroke-width="1.5"/><path d="M1.5 8h13M8 1.5c-3 3.5-3 9.5 0 13M8 1.5c3 3.5 3 9.5 0 13" fill="none" stroke="#fff" stroke-width="1.2"/></svg></p>
  </div>
</section>

</body>
</html>
```